International Clinical Software Company needs a new business card design

We are looking for a new business card design for our company that has recently expanded into the UK market, making us a multinational company.
After having rebranded our website and produced a new style guide, we are looking for a business card that is creative and attention grabbing, while being consistent with the style and colour scheme used on the new website, www.plumvora.example
We produce care management technology for the aged care market, but the main aspect we aim to communicate is the human element of our software, and the way it assists in providing better care for aged people, and stronger relationships between aged people and the staff that care for them.
Our current business card is a dark green with gold text, which makes the text quite difficult to read, not very aesthetically appealing and the colour scheme looks quite dated.
We would like something fresh and modern, that can still be colourful but doesn't use large blocks of dark colour, and uses the colours within our logo.
Something tying in with the leaves that are used in our logo could work quite nicely, along with the Autumn/Fall colours of soft greens, yellows and reds (also in our existing logo). However also happy to look at fresh, completely out of the box ideas we may not have yet considered.
Target Market(s)
The people that receive this business card work in the aged card or health industry and are either corporate/management level staff or clinical (Registered Nurses, care workers etc.)
Industry/Entity Type
Health Product
Contact Information for Business Card
Company Name - BrindlewayCare
Company locations: United Kingdom, Australia, New Zealand
Staff Details:
Staff name: Derek Mallow
Staff job title: Executive Chairman
Staff email: d.mallow@plumvora.example
Office phone number: 01742 918576
Font styles to use
Other font styles liked:
- Calibri
Requirements
Must have
- Must include the BrindlewayCare brand name in it's current font
- Must include logo (3 leaves in gold circle)
- Must include Business Card Details
Nice to have
- Elements of gold
- White space
- Something autumn themed but not too cliched
Should not have
- No blue - used by a major competitor and we would like to differentiate from them
- Large blocks of dark green colour (the green that appears in our leaves on the logo on our current business card is the background colour and it is far too dark)

```html
<!DOCTYPE html>
<html lang="en">
<head>
<meta charset="utf-8">
<title>BrindlewayCare — Business Card</title>
<link rel="stylesheet" href="https://fonts.googleapis.com/css2?family=Arimo:wght@400;700&display=swap">
<style>
  :root {
    --backdrop: #3a3b3d;
    --card: #ffffff;
    --gold: #c3b08a;
    --gold-deep: #b39c6e;
    --crimson: #c2185b;
    --ink: #6f6f6f;
    --rule: #e2e2e2;
  }
  * { box-sizing: border-box; margin: 0; padding: 0; }
  html, body {
    width: 1200px; height: 950px; overflow: hidden;
    background: var(--backdrop);
    font-family: "Arimo", Arial, sans-serif;
  }
  .business-card {
    position: absolute; left: 100px; top: 185px;
    width: 1000px; height: 580px;
    background: var(--card);
    box-shadow: 0 14px 40px rgba(0,0,0,.35);
    overflow: hidden;
  }
  .brand {
    position: absolute; left: 0; top: 110px; width: 470px;
    display: flex; flex-direction: column; align-items: center;
  }
  .brand-circle {
    width: 118px; height: 118px; border-radius: 50%;
    background: var(--gold);
  }
  .brand-name {
    margin-top: 26px;
    font-size: 44px; font-weight: 400; color: var(--gold-deep);
    letter-spacing: .5px;
  }
  .divider {
    position: absolute; left: 470px; top: 70px;
    width: 1px; height: 340px; background: var(--rule);
  }
  .contact {
    position: absolute; left: 520px; top: 80px; width: 460px;
    color: var(--ink);
  }
  .person-name { font-size: 34px; font-weight: 700; color: var(--gold-deep); }
  .person-title { font-size: 23px; color: var(--crimson); margin-top: 6px; }
  .locations { font-size: 22px; line-height: 1.3; margin-top: 18px; }
  .details { list-style: none; margin-top: 10px; font-size: 22px; }
  .details li { display: flex; align-items: center; gap: 12px; line-height: 1.45; }
  .details svg { width: 20px; height: 20px; flex: none; fill: var(--ink); }
  .footer-band {
    position: absolute; left: 0; bottom: 0; width: 100%; height: 92px;
    background: var(--gold);
  }
  .band-badge {
    position: absolute; right: 58px; bottom: 66px;
    width: 54px; height: 54px; border-radius: 50%;
    background: var(--card); border: 3px solid var(--gold);
  }
</style>
</head>
<body>
  <div class="business-card">
    <div class="brand">
      <div class="brand-circle"></div>
      <div class="brand-name">BrindlewayCare</div>
    </div>

    <div class="divider"></div>

    <div class="contact">
      <div class="person-name">Derek Mallow</div>
      <div class="person-title">Executive Chairman</div>
      <div class="locations">United Kingdom,<br>Australia, New Zealand</div>
      <ul class="details">
        <li>
          <svg viewBox="0 0 20 20" aria-hidden="true"><path d="M4 2h4l1.5 4-2.3 1.6a11 11 0 0 0 5.2 5.2L14 10.5l4 1.5v4c0 1.1-.9 2-2 2C8.3 18 2 11.7 2 4c0-1.1.9-2 2-2z"/></svg>
          <span>01742 918576</span>
        </li>
        <li>
          <svg viewBox="0 0 20 20" aria-hidden="true"><path d="M2 4h16v12H2z M2 4l8 6 8-6" fill="none" stroke="#6f6f6f" stroke-width="2"/></svg>
          <span>d.mallow@plumvora.example</span>
        </li>
        <li>
          <svg viewBox="0 0 20 20" aria-hidden="true"><circle cx="10" cy="10" r="8" fill="none" stroke="#6f6f6f" stroke-width="2"/><path d="M2 10h16M10 2c3 3 3 13 0 16M10 2c-3 3-3 13 0 16" fill="none" stroke="#6f6f6f" stroke-width="1.5"/></svg>
          <span>www.plumvora.example</span>
        </li>
      </ul>
    </div>

    <div class="footer-band"></div>
    <div class="band-badge"></div>
  </div>
</body>
</html>
```